Wordpress Design For Financial Investment Company

//** NEW WIREFRAME ADDED TO HELP WITH LAYOUT ISSUES. PLEASE REFER TO WIREFRAME IN ATTACHED FILES. NO DESIGN WILL BE CONSIDERED IF IT DOES NOT FOLLOW THE WIREFRAME. **//
//** PLEASE READ THE ENTIRE BRIEF INCLUDING ALL UPDATES TO THE BRIEF. THE CLIENT IS VERY SPECIFIC ABOUT WHAT THEY WANT AND I'VE COVERED SEVERAL THINGS IN THE UPDATES. THERE IS ALSO A VIDEO UPDATE THAT HAS SOME VALUABLE INFORMATION IN IT FOR THIS CONTEST. **//
The client is an investment advisor who needs a new website designed. The current site is http://www.velmorhold.example.
The client wants the site to be green to match the attached logo.
The home page should have relevant images in the rotator. No people hugging! This is a financial investment site, not a family counseling site.
Also, the client wants 4 buttons on the home page to highlight the 4 main areas they focus on:
Investment Advice and Education
General Financial Planning
Retirement Planning
401K Planning
The top right area of the site needs to have their phone number, a call to action, and 2 buttons.
Their phone number is 303-418-7719
The call to action should say something like "Call for a free consultation!"
The buttons need to say:
Login To Your Brokavell Account
Login To Your Quillbrook Account
The final design should communicate professionalism, financial safety and growth.
Main navigation should be:
Home
About Us
Associates
Services
Contact
Mission Statement (Could also be "Our Mission")
This is a site that the client likes: http://www.pkwadvisoryfirm.example/
Updates
The designs should not have:
Newsletter content. A newsletter sign up is fine
Learning Center
Calculators
Stock prices/tickers
The design should have a contact form on the page.
I have talked to my client and have some updates. I did a video update because I thought it would be easier to show what I'm trying to get across.
Reason: I am going to be extending the contest a few more days. I'm still not getting quite what I want and very few people are even trying to follow the creative brief and the updates to it.
PLEASE read the entire brief and the updates. There is also a video I made that explains everything. I've also attached a wireframe.
Thanks!
Target Market(s)
People looking for a high-end financial investment company.
Industry/Entity Type
Investment
Requirements
Must have
- !!FOLLOW THE WIREFRAME FOR LAYOUT!!
!!THEIR LOGO!!
4 buttons to highlight their main practice areas
Phone number in the top right
"Free Consultation" call to action
2 Login buttons in the top right
A contact form on the page.
Should not have
- The designs should not have:
Learning Center
Calculators
Stock prices/tickers

```html
<!DOCTYPE html>
<html lang="en">
<head>
<meta charset="utf-8">
<title>Velmor Financial — Home</title>
<link rel="stylesheet" href="https://fonts.googleapis.com/css2?family=Arimo:ital,wght@0,400;0,700;1,400;1,700&family=PT+Sans:ital,wght@0,700;1,700&family=Roboto+Condensed:wght@400;700&display=swap">
<style>
:root{
  --outer:#f8e9cb;
  --page:#fdf6e1;
  --page-edge:#e6d6b5;
  --green:#36694f;
  --green-dark:#2c5943;
  --green-head:#3d7a5a;
  --text:#555049;
  --text-dark:#3f3b36;
  --rule:#d9c9a7;
  --card:#fbf7e6;
  --field:#fbf8e7;
  --field-border:#d8c89f;
  --btn-dark:#1f1f1f;
  --white:#ffffff;
}
*{margin:0;padding:0;box-sizing:border-box}
html,body{width:1200px;height:1000px;overflow:hidden}
body{background:var(--outer);font-family:"Arimo",Arial,sans-serif;color:var(--text);position:relative}
.page{position:absolute;left:270px;top:0;width:660px;height:1000px;background:var(--page);border-left:2px solid var(--page-edge);border-right:2px solid var(--page-edge)}

/* top bar */
.login{position:absolute;top:13px;width:74px;height:22px;border:1px solid #d8c39a;border-radius:3px;background:linear-gradient(#f6e7c8,#ead5ab);display:flex;align-items:center;gap:4px;padding-left:4px;font-size:5.5px;font-weight:700;line-height:1.15;color:#4a4336}
.login svg{flex:none}
.consult{position:absolute;top:20px;right:334px;display:flex;align-items:center;gap:5px;font-size:7px;color:#6a6357}
.consult strong{font-family:"Roboto Condensed",sans-serif;font-size:12px;color:var(--text-dark);margin-left:4px;font-weight:700}

/* nav */
.nav{position:absolute;left:329px;top:41px;width:542px;height:29px;background:linear-gradient(#5a8f70,#3f7458);border-top:2px solid #8a6e4a}
.nav a{position:absolute;top:6px;font-size:10.5px;color:var(--white);text-decoration:none;transform:translateX(-50%);padding:2px 5px}
.nav a.active{background:var(--green-dark);border-radius:2px}
.brand{position:absolute;left:568px;top:23px;width:64px;height:64px;border-radius:50%;background:#e6d8cc;border:3px solid #1e1e1e;display:flex;flex-direction:column;align-items:center;justify-content:center;font-family:"Arimo",sans-serif;font-weight:700;color:#1e1e1e;text-align:center;line-height:1.25}
.brand .name{font-size:9px;letter-spacing:.5px}
.brand .sub{font-size:6px}

/* hero */
.hero{position:absolute;left:329px;top:70px;width:542px;height:260px;background:var(--green)}
.quote{position:absolute;top:23px;width:100%;text-align:center;font-size:8.5px;font-style:italic;color:var(--white)}
.quote b{font-weight:700}
.slider{position:absolute;left:4px;top:44px;width:534px;height:212px;background:var(--white);padding:5px}
.slide-photo{width:524px;height:202px;background:linear-gradient(90deg,#d9e3ea 0%,#b9cad8 35%,#9db7c4 60%,#8fa9ad 100%)}
.caption{position:absolute;left:335px;top:38px;width:194px;height:106px;background:rgba(70,90,85,.72);padding:12px 10px 0 38px;color:var(--white)}
.caption h2{font-family:"Roboto Condensed",sans-serif;font-weight:400;font-size:15px;line-height:21px}
.caption p{font-size:7.5px;line-height:10.5px;text-align:justify;margin-top:5px}

/* service cards */
.card{position:absolute;width:124px;height:150px;background:var(--card);border:1px solid #e3d9bc}
.card h3{height:16px;background:var(--green);color:var(--white);font-family:"Roboto Condensed",sans-serif;font-weight:700;font-size:8.5px;line-height:16px;text-align:center}
.card .photo{height:52px}
.card h4{font-size:8px;font-weight:700;color:var(--text-dark);text-align:center;margin-top:6px}
.card p{font-size:6.8px;line-height:10px;text-align:center;margin:2px 4px 0}
.card .btn{display:block;margin:5px auto 0;width:38px;height:15px;background:var(--btn-dark);color:var(--white);font-size:6.5px;line-height:15px;text-align:center;border-radius:2px}

/* intro column */
.intro{position:absolute;left:607px;top:347px;width:258px}
.heading{font-family:"PT Sans",sans-serif;font-style:italic;font-weight:700;color:var(--green-head);font-size:13.5px}
.body{font-size:6.8px;line-height:10.2px;color:var(--text)}
.intro .body{margin-top:7px}
.intro .body+.body{margin-top:10px}
.featured{position:absolute;left:607px;top:495px;width:258px}
.featured .title{display:flex;align-items:center;gap:10px}
.featured h5{font-family:"Arimo",sans-serif;font-style:italic;font-weight:700;color:var(--text-dark);font-size:9.5px;margin-top:8px}
.featured .body{margin-top:3px}
.green-btn{display:inline-block;background:var(--green);color:var(--white);font-style:italic;font-weight:700;font-size:6.5px;border-radius:3px;text-align:center}

/* blog */
.blog{position:absolute;left:335px;top:684px;width:294px;height:262px}
.blog>.heading{border-bottom:1px solid var(--rule);padding-bottom:6px}
.post{position:absolute;left:0;width:294px;height:70px}
.post .thumb{position:absolute;left:0;top:0;width:46px;height:46px}
.post h6{position:absolute;left:55px;top:1px;font-style:italic;font-weight:700;font-size:9.5px;color:var(--text-dark)}
.post .body{position:absolute;left:55px;top:15px;width:236px}
.post .meta{position:absolute;left:0;top:52px;width:294px;border-top:1px solid var(--rule);padding-top:2px;font-size:6.5px;font-style:italic;color:var(--text-dark)}
.post .meta span{margin-left:14px}
.post .more{position:absolute;right:0;top:55px;width:34px;height:12px;line-height:12px;font-size:5.5px}

/* contact */
.divider{position:absolute;left:645px;top:705px;width:1px;height:235px;background:var(--rule)}
.contact{position:absolute;left:650px;top:703px;width:215px}
.contact .title{display:flex;align-items:center;gap:10px;border-bottom:1px solid var(--rule);padding-bottom:5px}
.contact .title h2{font-style:italic;font-weight:700;font-size:11px;color:#837a6c}
.field{position:relative;height:29.5px}
.field label{position:absolute;left:1px;top:7px;font-size:6.5px;font-style:italic;color:#6f685c}
.field .input{position:absolute;left:50px;top:0;width:165px;height:19px;background:var(--field);border:1px solid var(--field-border);border-radius:4px}
.submit{position:absolute;left:814px;top:917px;width:51px;height:17px;line-height:17px;font-size:8px}

/* footer */
.footer{position:absolute;left:329px;top:962px;width:542px;height:38px;background:var(--green);color:var(--white);font-size:7px}
.footer .links{position:absolute;top:13px}
.footer .links a{color:var(--white);text-decoration:none}
.footer .links i{font-style:normal;margin:0 4px}
</style>
</head>
<body>
<div class="page"></div>

<header>
  <a class="login" style="left:329px"><svg width="12" height="12" viewBox="0 0 12 12"><rect width="12" height="12" rx="2" fill="#3e6b55"/><rect x="3.5" y="5.5" width="5" height="4" fill="#fff"/><path d="M4.5 5.5V4a1.5 1.5 0 0 1 3 0v1.5" stroke="#fff" fill="none"/></svg><span>Login to your<br>Brokavell Account</span></a>
  <a class="login" style="left:405px"><svg width="12" height="12" viewBox="0 0 12 12"><rect width="12" height="12" rx="2" fill="#3e6b55"/><rect x="3.5" y="5.5" width="5" height="4" fill="#fff"/><path d="M4.5 5.5V4a1.5 1.5 0 0 1 3 0v1.5" stroke="#fff" fill="none"/></svg><span>Login to your<br>Quillbrook Account</span></a>
  <div class="consult"><svg width="11" height="11" viewBox="0 0 11 11"><circle cx="5.5" cy="5.5" r="5.5" fill="#3e6b55"/><path d="M3.6 2.8l1 1.3-.6.8a4 4 0 0 0 1.9 1.9l.8-.6 1.3 1-.5 1c-2.6-.2-4.4-2-4.6-4.6z" fill="#fff"/></svg>Call for a free consultation <strong>303 418 7719</strong></div>
</header>

<nav class="nav">
  <a class="active" style="left:53px">Home</a>
  <a style="left:109px">About Us</a>
  <a style="left:175px">Associates</a>
  <a style="left:359px">Services</a>
  <a style="left:425px">Our Mission</a>
  <a style="left:490px">Contact</a>
</nav>
<div class="brand"><span class="name">VELMOR</span><span class="sub">Financial, Inc</span></div>

<section class="hero">
  <p class="quote">"Always do the right thing. This will gratify some people and astonish the rest" <b>-Elias Hartwell.</b></p>
  <div class="slider">
    <div class="slide-photo" role="img" aria-label="Two advisors at a desk in a bright office with a growth chart on a wall screen"></div>
    <div class="caption">
      <h2>Lorem Ipsum is simply of the printing</h2>
      <p>Lorem Ipsum is simply dummy text of the printing and typesetting industry. Lorem Ipsum has been the industry's standard dummy text ever since the 1500s,</p>
    </div>
  </div>
</section>

<section class="services">
  <article class="card" style="left:335px;top:350px"><h3>Investment Advice and Education</h3><div class="photo" role="img" aria-label="Stacked paper files" style="background:linear-gradient(#c9b998,#8f7b5c)"></div><h4>Lorem Ipsum is simply dummy</h4><p>Lorem Ipsum is simply dummy text of the printing and typesetting industry. Lorem Ipsum has been the industry's standard dummy text</p><a class="btn">Submit</a></article>
  <article class="card" style="left:471px;top:350px"><h3>Investment Advice and Education</h3><div class="photo" role="img" aria-label="Two smiling business professionals" style="background:linear-gradient(90deg,#e6e6ea,#9aa1ad 45%,#e7e3e0)"></div><h4>Lorem Ipsum is simply dummy</h4><p>Lorem Ipsum is simply dummy text of the printing and typesetting industry. Lorem Ipsum has been the industry's standard dummy text</p><a class="btn">Submit</a></article>
  <article class="card" style="left:335px;top:513px"><h3>Investment Advice and Education</h3><div class="photo" role="img" aria-label="Pen resting on a financial chart" style="background:linear-gradient(135deg,#dfe7df,#b9cbbf)"></div><h4>Lorem Ipsum is simply dummy</h4><p>Lorem Ipsum is simply dummy text of the printing and typesetting industry. Lorem Ipsum has been the industry's standard dummy text</p><a class="btn">Submit</a></article>
  <article class="card" style="left:471px;top:513px"><h3>Investment Advice and Education</h3><div class="photo" role="img" aria-label="Business team meeting around a table" style="background:linear-gradient(#eef0f3,#8d939c)"></div><h4>Lorem Ipsum is simply dummy</h4><p>Lorem Ipsum is simply dummy text of the printing and typesetting industry. Lorem Ipsum has been the industry's standard dummy text</p><a class="btn">Submit</a></article>
</section>

<section class="intro">
  <h2 class="heading">Velmor Financial .inc</h2>
  <p class="body">Lorem Ipsum is simply dummy text of the printing and typesetting industry. Lorem Ipsum has been the industry's standard dummy text ever since the 1500s, when an unknown printer took a galley of type and scrambled it to make a type specimen book. It has survived not only five centuries, but also the leap into electronic typesetting, remaining essentially unchanged. It was popularised in the 1960s with the release of Typeline sheets containing Lorem Ipsum passages, and more recently with desktop publishing software like Pagewright Studio including versions of Lorem Ipsum.</p>
  <p class="body">Lorem Ipsum is simply dummy text of the printing and typesetting industry. Lorem Ipsum has been the industry's standard dummy text ever since the 1500s, when an unknown printer took a galley.</p>
</section>

<section class="featured">
  <div class="title">
    <svg width="33" height="33" viewBox="0 0 33 33"><path d="M3 4h22l5 4v22H8l-5-4z" fill="#e8e4dc" stroke="#c9c2b5"/><rect x="8" y="17" width="4" height="11" fill="#c43c3c"/><rect x="13" y="12" width="4" height="16" fill="#3c7ac4"/><rect x="18" y="15" width="4" height="13" fill="#e0b83a"/><rect x="23" y="10" width="4" height="18" fill="#4aa55a"/></svg>
    <h2 class="heading">Velmor Featured</h2>
  </div>
  <h5>Lorem Ipsum is simply dummy text of the printing</h5>
  <p class="body">Lorem Ipsum is simply dummy text of the printing and typesetting industry. Lorem Ipsum has been the industry's standard dummy text ever since the 1500s, when an unknown printer took.</p>
  <h5>Lorem Ipsum is simply dummy text of the printing</h5>
  <p class="body">Lorem Ipsum is simply dummy text of the printing and typesetting industry. Lorem Ipsum has been the industry's standard dummy text ever since the 1500s, when an unknown printer took.</p>
  <a class="green-btn" style="margin-top:10px;width:52px;height:17px;line-height:17px">Read More</a>
</section>

<section class="blog">
  <h2 class="heading">Latest From Blog</h2>
  <article class="post" style="top:36px">
    <div class="thumb" role="img" aria-label="Two colleagues reviewing work" style="background:linear-gradient(#dfe3e6,#8a9098)"></div>
    <h6>Lorem Ipsum is simply dummy text of</h6>
    <p class="body">Lorem Ipsum is simply dummy text of the printing and typesetting industry. Lorem Ipsum has been the industry's standard dummy text ever since the 1500s, when an unknown printer took.</p>
    <p class="meta">Posted by: Admin, <span>25 July 2012</span></p>
    <a class="green-btn more">Read More</a>
  </article>
  <article class="post" style="top:112px">
    <div class="thumb" role="img" aria-label="Group of advisors in discussion" style="background:linear-gradient(#e4e5e8,#9ea3aa)"></div>
    <h6>Lorem Ipsum is simply dummy text of</h6>
    <p class="body">Lorem Ipsum is simply dummy text of the printing and typesetting industry. Lorem Ipsum has been the industry's standard dummy text ever since the 1500s, when an unknown printer took.</p>
    <p class="meta">Posted by: Admin, <span>25 July 2012</span></p>
    <a class="green-btn more">Read More</a>
  </article>
  <article class="post" style="top:192px">
    <div class="thumb" role="img" aria-label="Small team portrait" style="background:linear-gradient(#e9e4e1,#a39a94)"></div>
    <h6>Lorem Ipsum is simply dummy text of</h6>
    <p class="body">Lorem Ipsum is simply dummy text of the printing and typesetting industry. Lorem Ipsum has been the industry's standard dummy text ever since the 1500s, when an unknown printer took.</p>
    <p class="meta">Posted by: Admin, <span>25 July 2012</span></p>
    <a class="green-btn more">Read More</a>
  </article>
</section>

<div class="divider"></div>
<section class="contact">
  <div class="title">
    <svg width="28" height="22" viewBox="0 0 28 22"><rect x="1" y="1" width="26" height="20" fill="#fff" stroke="#b9b0a2"/><path d="M1 1h26" stroke="#c0474a" stroke-width="2" stroke-dasharray="3 2"/><path d="M1 21h26" stroke="#4863a8" stroke-width="2" stroke-dasharray="3 2"/><path d="M2 2l12 10L26 2" stroke="#b9b0a2" fill="none"/></svg>
    <h2>Contact Us</h2>
  </div>
  <div style="margin-top:12px">
    <div class="field"><label>First Name *</label><span class="input"></span></div>
    <div class="field"><label>Last Name *</label><span class="input"></span></div>
    <div class="field"><label>Email *</label><span class="input"></span></div>
    <div class="field"><label>Company *</label><span class="input"></span></div>
    <div class="field"><label>Message *</label><span class="input" style="height:48px"></span></div>
  </div>
</section>
<a class="green-btn submit">Contact Us</a>

<footer class="footer">
  <div class="links" style="left:13px"><a>Home</a><i>|</i><a>About Us</a><i>|</i><a>Associates</a><i>|</i><a>Services</a><i>|</i><a>Our Mission</a><i>|</i><a>Contact</a></div>
  <div class="links" style="right:13px"><a>Privacy</a><i>|</i><a>Terms and conditions</a><i>|</i><a>Disclaimer</a></div>
</footer>
</body>
</html>
```